Bramblewick Forage Business Cards

I need a business card with my logo, number, Facebook account, and some information about what I am selling. Green card with logo on the front. 555-214-8392 phone number, @bramblewickforage Facebook, •Orchardgrass Hay •Alfalfa Hay •Mixed Grass Hay , and “Premium Quality Hay” all written on the back.

Target Market(s)

Hay

Contact Information for Business Card

Phone number, Facebook, different types of hay.

Colors
00AB8E
00BBA5
67D7C9
C6EFE9
E9F9F6

```html
<!DOCTYPE html>
<html lang="en">
<head>
<meta charset="utf-8">
<title>Bramblewick Forage Business Cards</title>
<link rel="stylesheet" href="https://fonts.googleapis.com/css2?family=Arimo:wght@400;700&display=swap">
<style>
  :root {
    --backdrop: #2a2a2a;
    --card: #0d0d0d;
    --card-edge: #1c1c1c;
    --accent: #13a84f;
    --text-light: #f2f2f2;
    --text-muted: #c9c9c9;
    --silver: #bdbdbd;
    --rule: #3a3a3a;
  }
  * { margin: 0; padding: 0; box-sizing: border-box; }
  html, body {
    width: 1200px; height: 900px; overflow: hidden;
    background: var(--backdrop);
    font-family: "Arimo", Arial, sans-serif;
  }
  .sheet {
    width: 1200px; height: 900px;
    display: flex; align-items: center; justify-content: center; gap: 50px;
  }
  .card {
    position: relative;
    width: 540px; height: 309px;
    background: var(--card);
    border: 1px solid var(--card-edge);
    border-radius: 18px;
    overflow: hidden;
  }

  /* Contact side */
  .brand-row {
    position: absolute; left: 70px; top: 62px;
    display: flex; align-items: center; gap: 22px;
  }
  .brand-mark {
    width: 84px; height: 84px; border-radius: 50%;
    background: var(--accent);
  }
  .brand-divider { width: 1px; height: 86px; background: var(--rule); }
  .brand-name {
    color: var(--text-light); font-weight: 700; font-size: 30px; line-height: 1.1;
  }
  .contact-row {
    position: absolute; left: 100px; top: 180px;
    display: flex; align-items: center; gap: 28px;
  }
  .contact {
    display: flex; align-items: center; gap: 8px;
    color: var(--text-light); font-size: 15px;
  }
  .contact-icon {
    width: 26px; height: 26px; border-radius: 50%;
    background: var(--accent);
    display: flex; align-items: center; justify-content: center;
  }
  .contact-rule {
    position: absolute; left: 140px; right: 100px; top: 222px;
    height: 1px; background: linear-gradient(90deg, transparent, var(--rule), transparent);
  }
  .products {
    position: absolute; left: 0; right: 0; top: 236px;
    text-align: center; color: var(--text-muted); font-size: 15px; line-height: 1.45;
  }
  .products .dot {
    display: inline-block; width: 8px; height: 8px; border-radius: 50%;
    background: var(--accent); margin: 0 8px; vertical-align: middle;
  }

  /* Front side */
  .front-lockup {
    position: absolute; left: 0; right: 0; top: 0; bottom: 0;
    display: flex; align-items: center; justify-content: center; gap: 22px;
  }
  .front-mark {
    width: 92px; height: 92px; border-radius: 50%;
    background: var(--silver);
  }
  .front-name { color: var(--silver); font-weight: 700; font-size: 26px; }
  .front-phone { color: var(--silver); font-weight: 700; font-size: 30px; margin-top: 6px; }
</style>
</head>
<body>
<main class="sheet">
  <section class="card card--contact" aria-label="Card back with contact details">
    <div class="brand-row">
      <div class="brand-mark"></div>
      <div class="brand-divider"></div>
      <div class="brand-name">Bramblewick Forage</div>
    </div>

    <div class="contact-row">
      <div class="contact">
        <span class="contact-icon">
          <svg width="14" height="14" viewBox="0 0 24 24" aria-hidden="true">
            <path fill="#fff" d="M6.6 10.8a15.1 15.1 0 0 0 6.6 6.6l2.2-2.2a1 1 0 0 1 1-.25 11.4 11.4 0 0 0 3.6.57 1 1 0 0 1 1 1V20a1 1 0 0 1-1 1A17 17 0 0 1 3 4a1 1 0 0 1 1-1h3.5a1 1 0 0 1 1 1c0 1.25.2 2.45.57 3.6a1 1 0 0 1-.25 1z"/>
          </svg>
        </span>
        555-214-8392
      </div>
      <div class="contact">
        <span class="contact-icon"></span>
        @bramblewickforage
      </div>
    </div>

    <div class="contact-rule"></div>

    <p class="products">
      Orchardgrass Hay<span class="dot"></span>Alfalfa Hay<span class="dot"></span>Mixed Grass Hay<br>
      Premium Quality Hay
    </p>
  </section>

  <section class="card card--front" aria-label="Card front">
    <div class="front-lockup">
      <div class="front-mark"></div>
      <div>
        <div class="front-name">Bramblewick Forage</div>
        <div class="front-phone">555-214-8392</div>
      </div>
    </div>
  </section>
</main>
</body>
</html>
```